Restyle corporate identity (+ logo) for a road construction company

We need a new logo and stationary design for our company VARNOK path. VARNOK path® increases the road base strength, while reducing major costs and time of road construction. Attached some examples of the current design.

Our wishes for the new logo:
- Business look
- Style sheet
- Modern

More information: www.varnokpath.example
Updates

Target Market(s)

Government

Industry/Entity Type

Construction

Requirements
Must have
• Logo (with road sign) + text

```html
<!DOCTYPE html>
<html lang="en">
<head>
<meta charset="utf-8">
<title>VARNOK PATH – Business Card</title>
<link href="https://fonts.googleapis.com/css2?family=Open+Sans:wght@400;600&display=swap" rel="stylesheet">
<style>
  :root {
    --backdrop: #8a8a8a;
    --card-white: #ececec;
    --brand-blue: #1380e6;
    --ink: #4a4a4a;
    --white: #ffffff;
    --soft-white: #e6eef8;
  }
  * { box-sizing: border-box; margin: 0; padding: 0; }
  html, body {
    width: 1105px; height: 1200px; overflow: hidden;
    background: var(--backdrop);
    font-family: "Open Sans", Arial, sans-serif;
  }
  .canvas { position: relative; width: 1105px; height: 1200px; }
  .card {
    position: absolute; left: 182px; width: 746px; height: 427px;
  }
  .card--front { top: 119px; background: var(--card-white); }
  .card--back { top: 637px; background: var(--brand-blue); }

  .name-band {
    position: absolute; left: 0; top: 55px; width: 425px; height: 97px;
    background: var(--brand-blue); color: var(--white);
    padding: 22px 0 0 52px;
  }
  .person-name { font-size: 26px; font-weight: 600; letter-spacing: 0.5px; line-height: 1.1; }
  .person-role { font-size: 19px; font-weight: 400; margin-top: 4px; }

  .wordmark {
    position: absolute; display: flex; align-items: center; gap: 12px;
    font-weight: 600; letter-spacing: 2px; white-space: nowrap;
  }
  .wordmark__square { display: block; }
  .card--front .wordmark { left: 420px; top: 62px; color: var(--brand-blue); font-size: 34px; }
  .card--front .wordmark__square { width: 40px; height: 40px; background: var(--brand-blue); }
  .card--back .wordmark {
    left: 50%; top: 160px; transform: translateX(-50%);
    color: var(--soft-white); font-size: 44px;
  }
  .card--back .wordmark__square { width: 54px; height: 54px; background: var(--soft-white); }

  .contact-list {
    position: absolute; left: 52px; top: 300px; list-style: none;
    color: var(--ink); font-size: 19px; line-height: 28.5px;
  }
  .contact-list li { display: flex; align-items: center; gap: 10px; }
  .contact-list svg { width: 17px; height: 17px; fill: var(--brand-blue); flex: none; }

  .address {
    position: absolute; right: 46px; top: 300px; text-align: right;
    font-style: normal; color: var(--ink); font-size: 19px; line-height: 28.5px;
  }

  .back-url {
    position: absolute; left: 0; right: 0; top: 356px; text-align: center;
    color: var(--soft-white); font-size: 18px; letter-spacing: 4px;
  }
</style>
</head>
<body>
<div class="canvas">
  <section class="card card--front">
    <div class="name-band">
      <p class="person-name">MARTEN VOS</p>
      <p class="person-role">CEO/Founder</p>
    </div>
    <div class="wordmark"><span class="wordmark__square"></span>VARNOK PATH</div>

    <ul class="contact-list">
      <li>
        <svg viewBox="0 0 24 24" aria-hidden="true"><path d="M6.6 10.8a15.1 15.1 0 0 0 6.6 6.6l2.2-2.2a1 1 0 0 1 1-.25 11.4 11.4 0 0 0 3.6.57 1 1 0 0 1 1 1V20a1 1 0 0 1-1 1A17 17 0 0 1 3 4a1 1 0 0 1 1-1h3.5a1 1 0 0 1 1 1c0 1.25.2 2.45.57 3.57a1 1 0 0 1-.25 1z"/></svg>
        614 208 7391
      </li>
      <li>
        <svg viewBox="0 0 24 24" aria-hidden="true"><path d="M2 5h20v14H2z M2 5l10 8 10-8" fill="var(--brand-blue)"/><path d="M2 6l10 7.5L22 6" fill="none" stroke="#ececec" stroke-width="1.6"/></svg>
        mail@varnokpath.example
      </li>
      <li>
        <svg viewBox="0 0 24 24" aria-hidden="true"><circle cx="12" cy="12" r="10"/><path d="M2 12h20M12 2c3 3 3 17 0 20M12 2c-3 3-3 17 0 20" fill="none" stroke="#ececec" stroke-width="1.4"/></svg>
        www.varnokpath.example
      </li>
    </ul>

    <address class="address">
      Lindenkade 58<br>
      4811 AB Breda<br>
      The Netherlands
    </address>
  </section>

  <section class="card card--back">
    <div class="wordmark"><span class="wordmark__square"></span>VARNOK PATH</div>
    <p class="back-url">www.varnokpath.example</p>
  </section>
</div>
</body>
</html>
```